Business card for a Exhibition booth fabrication company

Hi. My company would like to change our corporate name card. We are an events and Exhibition stand builder company. We would like our corporate name card to resonate what we do. I need someone to create something unique that relates to the industry that I am in. The graphic designer should be creative to incorporate the elements of my industry and try to blend in well in the design of the card. Our aim is to ensure that we are unique and our card can look different from our competitors.
Updates

Target Market(s)

Marketing and events manager from all companies

Contact Information for Business Card

The business card should have the following details:
Name
Job Title
Email
Website

Colors

Designer to choose colors to be used in the design.

Requirements
Must have
• The card must be look something that is relevant to the service that I am providing. My website is: www.velmora-buildworks.com
• You can see my website to get more information on what service that I am doing
Nice to have
• On the back of my card, I would like to have a globe image with the incorporation of my company logo. This is to indicate that my services can be done in any part of the world.

```html
<!DOCTYPE html>
<html lang="en">
<head>
<meta charset="utf-8">
<title>Velmora Buildworks – Business Card</title>
<link href="https://fonts.googleapis.com/css2?family=Michroma&family=Lato:wght@400;700&display=swap" rel="stylesheet">
<style>
  :root {
    --stage: #d9d9db;
    --card: #2b2b2d;
    --card-edge: #232325;
    --red: #e3222a;
    --red-deep: #a3151b;
    --white: #f4f4f4;
    --muted: #bfbfc2;
    --globe-light: #9a9a9c;
    --globe-dark: #3a3a3c;
  }
  * { box-sizing: border-box; margin: 0; padding: 0; }
  html, body { width: 1200px; height: 900px; overflow: hidden; background: var(--stage); }
  .stage {
    width: 1200px; height: 900px;
    display: flex; flex-direction: column; align-items: center; justify-content: center; gap: 30px;
  }
  .card {
    position: relative; width: 700px; height: 400px;
    background: var(--card); overflow: hidden;
    box-shadow: 0 6px 18px rgba(0,0,0,.25);
  }

  /* Back */
  .card-back { background: linear-gradient(135deg, var(--card-edge), var(--card)); }
  .globe-art {
    position: absolute; left: 215px; top: 45px; width: 310px; height: 310px; border-radius: 50%;
    background: radial-gradient(circle at 65% 40%, var(--globe-light) 0%, #6a6a6c 40%, var(--globe-dark) 80%);
  }
  .back-name {
    position: absolute; left: 0; right: 0; top: 185px; text-align: center;
    font-family: "Michroma", sans-serif; font-size: 26px; letter-spacing: 2px; color: var(--red);
  }

  /* Front */
  .brand {
    position: absolute; left: 60px; top: 150px; width: 300px;
    display: flex; flex-direction: column; align-items: center; gap: 18px;
  }
  .brand-dot { width: 44px; height: 44px; border-radius: 50%; background: var(--red); }
  .brand-name {
    font-family: "Michroma", sans-serif; font-size: 20px; letter-spacing: 2px;
    color: var(--white); text-align: center; line-height: 1.3;
  }
  .divider { position: absolute; left: 395px; top: 110px; width: 1px; height: 190px; background: var(--muted); }
  .contact { position: absolute; left: 425px; top: 110px; font-family: "Lato", sans-serif; color: var(--white); }
  .person-name {
    font-family: "Michroma", sans-serif; font-size: 22px; letter-spacing: 1.5px; color: var(--red);
  }
  .person-title { font-size: 16px; letter-spacing: .5px; margin: 4px 0 14px; }
  .contact-list { list-style: none; }
  .contact-list li { display: flex; align-items: center; gap: 10px; font-size: 16px; letter-spacing: .5px; margin-bottom: 7px; }
  .contact-list svg { width: 13px; height: 13px; flex: none; fill: var(--red); }
  .edge-band {
    position: absolute; left: 0; right: 0; bottom: 0; height: 14px;
    background: linear-gradient(90deg, var(--red), var(--red-deep) 45%, var(--red) 100%);
  }
</style>
</head>
<body>
<main class="stage">
  <section class="card card-back">
    <div class="globe-art" role="img" aria-label="Grey world globe illustration behind the company name"></div>
    <p class="back-name">VELMORA BUILDWORKS</p>
  </section>

  <section class="card card-front">
    <div class="brand">
      <span class="brand-dot"></span>
      <p class="brand-name">VELMORA<br>BUILDWORKS</p>
    </div>
    <div class="divider"></div>
    <div class="contact">
      <h1 class="person-name">DANIEL ARDEN</h1>
      <p class="person-title">Founder &amp; CEO</p>
      <ul class="contact-list">
        <li><svg viewBox="0 0 24 24"><path d="M6.6 10.8a15.1 15.1 0 0 0 6.6 6.6l2.2-2.2c.3-.3.7-.4 1-.2 1.1.4 2.3.6 3.6.6.6 0 1 .4 1 1V20c0 .6-.4 1-1 1A17 17 0 0 1 3 4c0-.6.4-1 1-1h3.5c.6 0 1 .4 1 1 0 1.3.2 2.5.6 3.6.1.3 0 .7-.2 1z"/></svg>+65 81402276 (Singapore)</li>
        <li><svg viewBox="0 0 24 24"><path d="M6.6 10.8a15.1 15.1 0 0 0 6.6 6.6l2.2-2.2c.3-.3.7-.4 1-.2 1.1.4 2.3.6 3.6.6.6 0 1 .4 1 1V20c0 .6-.4 1-1 1A17 17 0 0 1 3 4c0-.6.4-1 1-1h3.5c.6 0 1 .4 1 1 0 1.3.2 2.5.6 3.6.1.3 0 .7-.2 1z"/></svg>+974 55128390 (Qatar)</li>
        <li><svg viewBox="0 0 24 24"><path d="M2 5h20v14H2z M2 5l10 8 10-8" /></svg>info@velmora-buildworks.com</li>
        <li><svg viewBox="0 0 24 24"><circle cx="12" cy="12" r="10" fill="none" stroke="#e3222a" stroke-width="2"/><path d="M2 12h20M12 2c3 3 3 17 0 20M12 2c-3 3-3 17 0 20" fill="none" stroke="#e3222a" stroke-width="2"/></svg>www.velmora-buildworks.com</li>
      </ul>
    </div>
    <div class="edge-band"></div>
  </section>
</main>
</body>
</html>
```